New Business Card for Web Design/Internet Marketing Company

Looking for a great looking new business card. We are a 10 year old web design, internet marketing and website management company that works mostly with small businesses.

Our new card needs to better match the colors and style of our website, be bold, extremely usable and slightly edgy.

Target Market(s)

Small/Medium businesses that have websites

Industry/Entity Type

Internet

Requirements
Must have
• Front and back design, full color, rounded corners please

Must use the colors/style of our website (JPG provided)

INFO FOR CARDS (as readable as possible please)
Mark Lenner
President/CEO
mark@trelvanmedia.example
Phone: 520-381-7459
Toll Free: 866-381-7459
Address: 4315 W. Calloway Ave. Ste. 140, Tucson, AZ 85792

THINGS I WANT TO PROMOTE (if there is room):
1. Our Website - www.trelvanmedia.example

2. Social Media
Twitter: @trelvanmedia
Facebook: www.facebook.com/trelvanmedia

3. Our Services
Web Design
Internet Marketing
Website Management

```html
<!DOCTYPE html>
<html lang="en">
<head>
<meta charset="utf-8">
<title>Trelvan Media – Business Card</title>
<link href="https://fonts.googleapis.com/css2?family=Cabin:wght@400;500;600;700&family=Cabin+Condensed:wght@400;500&display=swap" rel="stylesheet">
<style>
  :root {
    --backdrop: #1c1c1c;
    --paper: #f4f4f2;
    --brand-blue: #1769ad;
    --brand-blue-light: #2380c9;
    --brand-blue-dark: #0c5595;
    --brand-orange: #e2671d;
    --text-grey: #4f4f4f;
    --heading-grey: #5a5a5a;
    --white: #ffffff;
  }
  * { margin: 0; padding: 0; box-sizing: border-box; }
  html, body { width: 1200px; height: 935px; overflow: hidden; }
  body {
    background: var(--backdrop);
    font-family: "Cabin", sans-serif;
    position: relative;
  }
  .card {
    position: absolute;
    width: 396px;
    height: 617px;
    overflow: hidden;
  }
  .card--back {
    left: 562px; top: 101px;
    background: linear-gradient(160deg, var(--brand-blue-light) 0%, var(--brand-blue) 55%, var(--brand-blue-dark) 100%);
  }
  .card--front {
    left: 242px; top: 217px;
    background: var(--paper);
    box-shadow: 0 4px 14px rgba(0,0,0,.45);
  }

  /* service stripes */
  .service {
    position: absolute;
    top: 0;
    width: 14px;
    display: flex;
    flex-direction: column;
    align-items: center;
  }
  .service__bar { width: 13px; }
  .service__label {
    writing-mode: vertical-rl;
    font-size: 15px;
    letter-spacing: 1.6px;
    line-height: 14px;
    margin-top: 6px;
    white-space: nowrap;
    text-transform: uppercase;
  }
  .card--front .service__bar { background: var(--brand-blue); }
  .card--front .service__label { color: var(--text-grey); }
  .card--back .service__bar { background: var(--white); }
  .card--back .service__label { color: var(--white); }
  .service--design { left: 320px; }
  .service--marketing { left: 342px; }
  .service--management { left: 364px; }
  .service--design .service__bar { height: 71px; }
  .service--marketing .service__bar { height: 101px; }
  .service--management .service__bar { height: 137px; }
  .card--back .service--design .service__bar { height: 79px; }
  .card--back .service--marketing .service__bar { height: 109px; }
  .card--back .service--management .service__bar { height: 148px; }

  /* front */
  .person { position: absolute; left: 26px; top: 54px; width: 214px; }
  .person__name {
    font-family: "Cabin Condensed", sans-serif;
    font-weight: 500;
    font-size: 41px;
    line-height: 44px;
    letter-spacing: -0.6px;
    white-space: nowrap;
  }
  .person__first { color: var(--brand-blue); }
  .person__last { color: var(--brand-orange); }
  .person__title {
    font-size: 20px;
    color: var(--text-grey);
    text-align: right;
    white-space: nowrap;
  }
  .section-heading {
    position: absolute;
    left: 22px;
    font-size: 25px;
    font-weight: 700;
    letter-spacing: -0.3px;
    color: var(--heading-grey);
    line-height: 30px;
  }
  .section-heading .accent { color: var(--brand-orange); }
  .section-heading--contact { top: 192px; }
  .section-heading--social { top: 480px; }

  .info-list { position: absolute; left: 22px; list-style: none; }
  .info-list--contact { top: 227px; }
  .info-list--social { top: 515px; }
  .info-list li {
    display: flex;
    align-items: flex-start;
    font-size: 19px;
    line-height: 27px;
    color: var(--text-grey);
    margin-bottom: 10px;
    white-space: nowrap;
  }
  .info-list li.address { line-height: 32px; margin-top: -3px; }
  .info-list li.address .icon-tag { margin-top: 6px; }
  .icon-tag {
    flex: 0 0 21px;
    width: 21px; height: 21px;
    margin-top: 3px;
    margin-right: 15px;
    border-radius: 3px;
    background: var(--brand-orange);
    color: var(--white);
    font-size: 14px;
    font-weight: 600;
    line-height: 20px;
    text-align: center;
  }
  .icon-tag--plain { background: var(--brand-blue-light); }
  .icon-tag--plain.dark { background: var(--brand-blue-dark); }
  .front-band {
    position: absolute;
    left: 0; bottom: 0;
    width: 103px; height: 18px;
    background: var(--brand-blue);
  }

  /* back brand mark */
  .brand {
    position: absolute;
    left: 0; right: 0;
    top: 412px;
    display: flex;
    flex-direction: column;
    align-items: center;
  }
  .brand__dot {
    width: 66px; height: 66px;
    border-radius: 50%;
    background: var(--brand-orange);
    margin-bottom: 12px;
  }
  .brand__name {
    font-size: 34px;
    font-weight: 700;
    color: var(--brand-orange);
    letter-spacing: 0.2px;
    line-height: 40px;
  }
</style>
</head>
<body>

<section class="card card--back" aria-label="Card back">
  <div class="service service--design"><span class="service__bar"></span><span class="service__label">Web Design</span></div>
  <div class="service service--marketing"><span class="service__bar"></span><span class="service__label">Internet Marketing</span></div>
  <div class="service service--management"><span class="service__bar"></span><span class="service__label">Website Management</span></div>
  <div class="brand">
    <span class="brand__dot"></span>
    <span class="brand__name">Trelvan Media</span>
  </div>
</section>

<section class="card card--front" aria-label="Card front">
  <div class="person">
    <div class="person__name"><span class="person__first">MARK</span> <span class="person__last">LENNER</span></div>
    <div class="person__title">President/CEO</div>
  </div>

  <div class="service service--design"><span class="service__bar"></span><span class="service__label">Web Design</span></div>
  <div class="service service--marketing"><span class="service__bar"></span><span class="service__label">Internet Marketing</span></div>
  <div class="service service--management"><span class="service__bar"></span><span class="service__label">Website Management</span></div>

  <h2 class="section-heading section-heading--contact"><span class="accent">CONTACT</span> US</h2>
  <ul class="info-list info-list--contact">
    <li><span class="icon-tag">p</span>520-381-7459</li>
    <li><span class="icon-tag">t</span>866-381-7459</li>
    <li><span class="icon-tag">e</span>mark@trelvanmedia.example</li>
    <li><span class="icon-tag">w</span>www.trelvanmedia.example</li>
    <li class="address"><span class="icon-tag">a</span><span>4315 W. Calloway Ave.<br>Ste. 140, Tucson, AZ 85792</span></li>
  </ul>

  <h2 class="section-heading section-heading--social"><span class="accent">SOCIAL</span> MEDIA</h2>
  <ul class="info-list info-list--social">
    <li><span class="icon-tag icon-tag--plain"></span>@trelvanmedia</li>
    <li><span class="icon-tag icon-tag--plain dark"></span>socialnook.example/trelvanmedia</li>
  </ul>

  <div class="front-band"></div>
</section>

</body>
</html>
```